Corporate website design needed

We need a Contemporary Industrial/Tech/Logistics Website design to match our logistic client's business. Our client consults and build logistics solutions that they manage but they are not a typical 3PL (3rd party logistics company) which is primarily engaged in moving boxes.
PSD file only for now, home and default templates.
COMPANY CHARACTER
DESIGN LOOK AND FEEL
• The design should also be modern and visually well organized — employing a combination of visual devices and info graphics. Keep it light and not too heavy but strong/ professional. And unique.
• The design should go beyond the typical industrial pick and pack 3PL representing [Logistics Company] as a High Tech/IT logistics company.
Some examples although these are not right for this client because they have much more content and present themselves more as a 3pl.
http://www.vobrelink-hub.example/ (More right then wrong - Like this but simplified)
http://www.durmaxfreight.example (Ugly)
http://www.tpwallerton.example (More right then wrong but different focus)
http://www.pelhamrye.example/ Too 3PL trucking… We want a bit ore high level approach
The difference, the design should be a fusion in core concepts that culminate in a design which implies the following attributes. Tech (Big data / analytics / software), Consultancy (Solutions, SME, Leader), 3PL Industry vertical solutions.
NOTE: The visualization of “tech” is not “1” and “0”, but more “software and analytics” Perhaps more like www.navimetra.example.
• They need to be seen as a solutions provider in Logistics and as in Subject matter experts
TONE
The tone needs to exude professionalism, expertise, though leadership along with technical and executional excellence.
Experienced
Knowledgeable
Confident
Determined
Straightforward
WEBSITE OBJECTIVES
• Focus C-Suite executives and logistics managers’ attention on [Logistics Company]s commanding knowledge and expertise, and unique approach to supply chain solutions producing more RFP wins
• Create an easy to scan design which decreases the reliance on text through featured text, summaries, and smaller “chunked” size bits of information.
• Convey [Logistics Company] as high-tech 3PL solutions developer and services provider with a ‘high-touch’ consultative approach.
• Showcase [Logistics Company]’s value propositions. (See Slider Content)
• Showcase [Logistics Company]’s expertise in logistical analytics.
• Gain recognition as an industry leader in evolutionary new space (supply chain 2.0)
WEBSITE STRATEGY
• Reduce reliance on text (at least within initial entry points for each section)
• Typography: Watch text line lengths and readability, bolder fonts. NO SERIFS
• Generally, create a click-through format so that users who want more details can find it, and those who don’t can get a snapshot without clicking through.
• Increase visual content through info graphics and some dynamic content, photography
• Better utilize the space on each page (e.g., add visual interest, photography and iconography where appropriate to break up copy blocks and maintain readable line lengths).
COLOR SCHEME
• Create a more engaging color scheme (the logo will remain the same under all circumstances).
• Red / grayscale may work…. Not too dark or heavy. Not too much red. Ex. quiltora.example
• Also try blues and greys. They seem to like that. Open to suggestions but don’t get to crazy. Red is in their logo but too much may be a problem.
PHOTOGRAPHY
Yes. And I will upload some.
If you pick photography please be sure to note Which stock house used and the image number!
CONTENT
The content will be presented in a more hierarchical format — with lead-ins, paragraph and section headers and navigational cues to expand lengthier content allowing the visitor to more easily scan the website. No case studies, No Social media, News while on the home page should not be over emphasized. They don't post a lot so it gets dated quickly ...
I will be uploading a wire frame and other elements.
NOTE: I uploaded my EXAMPLE mock up which is close but not close enough.
I am not a great designer. So I am looking for an alternative that exceed my design ability! These examples show the basic layout but I really want some varied alternatives.
The colors are inconsistent and type not quite right. The grey bar at top is not right and should probably go away.
Please pull the basic elements in the example together into a great design.
If you have questions please contact me.
i will upload some photography tomorrow that may be of use.
Thanks!
Updates
Hi All,
We are still evaluating the submitted designs. Sorry for the delay.
Target Market(s)
This website is primarily a validation website. Few new customers will search and find them as such...
The site should be Focused on C-Suite executives and logistics managers’ attention on [Logistics Company]s commanding knowledge and expertise, and unique approach to supply chain solutions producing more RFP wins
Industry/Entity Type
Business
Font styles to use
Requirements
Must have
- Slide show, Clearly explain who they are and what they do.
Create an easy to scan design which decreases the reliance on text through featured text, summaries, and smaller “chunked” size bits of information.
Convey [Logistics Company] as high-tech 3PL solutions developer and services
provider with a ‘high-touch’ consultative approach.
Should not have
- No Ads space
No Social media
Not too cluttered. Keep it clean.

```html
<!DOCTYPE html>
<html lang="en">
<head>
<meta charset="utf-8">
<title>Harlow Logistics</title>
<link href="https://fonts.googleapis.com/css2?family=Open+Sans:wght@400;600&family=Oswald:wght@300;400&family=Ubuntu:wght@500;700&display=swap" rel="stylesheet">
<style>
:root{
  --red:#c8102e;
  --topbar:#9b9b9b;
  --panel:#e9e9e9;
  --ink:#1f2a44;
  --body:#333;
  --muted:#666;
  --footer:#1b1b1b;
  --footer-base:#0f0f0f;
  --white:#fff;
}
*{margin:0;padding:0;box-sizing:border-box}
html,body{width:793px;height:1200px;overflow:hidden;background:var(--white)}
body{position:relative;font-family:"Open Sans",Arial,sans-serif;color:var(--body)}
a{color:inherit;text-decoration:none}
.abs{position:absolute}

.topbar{left:0;top:0;width:793px;height:28px;background:var(--topbar)}
.topbar-links{right:102px;top:7px;font-size:10px;color:var(--white);display:flex;gap:10px;white-space:nowrap}
.topbar-links .call{color:var(--red);margin-left:3px}
.topbar-links .call span{color:var(--white)}

.brand{left:76px;top:58px;display:flex;align-items:center;gap:8px}
.brand-mark{width:14px;height:14px;border-radius:50%;background:var(--red)}
.brand-name{font-size:17px;font-weight:600;letter-spacing:3px;color:#222;text-transform:uppercase}

.mainnav{top:69px;left:410px;display:flex;align-items:center;font-size:11px;color:#222}
.mainnav a{display:block;height:27px;line-height:27px}
.mainnav .active{background:var(--red);color:var(--white);width:80px;text-align:center}
.mainnav .n2{margin-left:40px}
.mainnav .n3{margin-left:46px}

.panel{left:76px;top:132px;width:641px;height:623px;background:var(--panel)}
.slide-shadow{top:140px;width:40px;height:230px;border-radius:50%;background:radial-gradient(ellipse at center,rgba(0,0,0,.55),rgba(0,0,0,0) 70%)}
.slide{left:78px;top:132px;width:636px;height:242px;border:2px solid var(--white);background:linear-gradient(90deg,#c3c6cc 0%,#a9adb5 22%,#c9b48a 40%,var(--red) 60%)}
.slide-title{left:426px;top:248px;font-family:Ubuntu,sans-serif;font-weight:700;font-size:20px;color:var(--white);letter-spacing:.6px;white-space:nowrap}
.slide-sub{left:490px;top:273px;width:224px;height:26px;background:var(--white);font-family:Ubuntu,sans-serif;font-weight:500;font-size:15px;color:#222;padding:4px 0 0 7px}
.slide-base{left:78px;top:376px;width:636px;height:26px;background:radial-gradient(ellipse at 50% 0,rgba(0,0,0,.25),rgba(0,0,0,0) 70%)}
.dots{left:363px;top:424px;display:flex;gap:5px}
.dots i{width:12px;height:12px;border-radius:50%;background:#f4f4f4;border:2px solid #cfcfcf}
.dots i.on{background:#555;border-color:#ddd}

.welcome-title{left:85px;top:472px;font-family:Oswald,sans-serif;font-weight:400;font-size:18px;color:var(--ink);white-space:nowrap}
.welcome-rule{left:305px;top:488px;width:401px;height:1px;background:#888}
.welcome-copy{left:87px;top:505px;width:616px;font-family:Arial,Helvetica,sans-serif;font-size:9.4px;line-height:11.9px;color:var(--body)}
.welcome-copy p+p{margin-top:12px}
.welcome-copy p.tight{margin-top:0}
.read-more{left:87px;top:643px;font-size:11px;font-weight:600;color:var(--red)}

.card{top:707px;width:149px;height:199px;background:var(--white);text-align:center}
.card-photo{display:block;width:74px;height:72px;border-radius:50%;margin:22px auto 0}
.card-title{margin-top:10px;font-size:11px;font-weight:400;color:var(--ink);letter-spacing:.5px}
.card-text{margin:3px 10px 0;font-family:Arial,sans-serif;font-size:7.6px;line-height:10px;color:var(--muted);text-align:justify;text-align-last:center}
.card-btn{position:absolute;left:0;bottom:0;width:149px;height:28px;line-height:28px;background:var(--red);color:var(--white);font-family:Arial,sans-serif;font-size:9.5px}

.partners{left:86px;top:932px;width:621px;height:52px;border-radius:14px;background:linear-gradient(#fff,#f4f4f4);border:3px solid #dedede;display:flex;align-items:center;justify-content:space-between;padding:0 14px}
.partner-row{display:flex;align-items:center;gap:26px}
.partner{height:26px;border-radius:4px;background:#d8d8d8}

.footer{left:0;top:1015px;width:793px;height:155px;background:var(--footer)}
.fcol{top:1044px;color:var(--white)}
.fcol h3{font-weight:400;font-size:14px;margin-bottom:8px}
.fcol li{list-style:none;font-size:8px;line-height:14.6px}
.fdiv{top:1046px;width:1px;height:86px;background:#3a3a3a}
.flogo{left:553px;top:1068px;display:flex;align-items:center;gap:8px}
.flogo .brand-mark{width:12px;height:12px}
.flogo .brand-name{font-size:12px;color:var(--white);letter-spacing:2.5px}
.basebar{left:0;top:1170px;width:793px;height:30px;background:var(--footer-base);font-size:7.6px;color:#ccc;padding:8px 0 0 104px;white-space:nowrap}
.basebar .sep{margin:0 3px}
.basebar .copy{margin-left:12px}
</style>
</head>
<body>

<header>
  <div class="abs topbar"></div>
  <nav class="abs topbar-links">
    <a href="#">Company</a><a href="#">Careers</a><a href="#">Contact</a>
    <span class="call">Call Us : <span>44(0)1632 960418</span></span>
  </nav>
  <div class="abs brand"><span class="brand-mark"></span><span class="brand-name">Harlow Logistics</span></div>
  <nav class="abs mainnav">
    <a class="active" href="#">SOLUTIONS</a>
    <a class="n2" href="#">OUR PROCESSES</a>
    <a class="n3" href="#">INDUSTRIES</a>
  </nav>
</header>

<main>
  <div class="abs panel"></div>
  <div class="abs slide-shadow" style="left:52px"></div>
  <div class="abs slide-shadow" style="left:701px"></div>
  <section class="abs slide" role="img" aria-label="Globe with shipping routes and a stack of cardboard boxes on a red background"></section>
  <h2 class="abs slide-title">There Are Many Variations</h2>
  <div class="abs slide-sub">New Way To Think</div>
  <div class="abs slide-base"></div>
  <div class="abs dots"><i class="on"></i><i></i><i></i><i></i></div>

  <h1 class="abs welcome-title">Welcome to Harlow Logistics</h1>
  <div class="abs welcome-rule"></div>
  <div class="abs welcome-copy">
    <p>simply dummy text of the printing and typesetting industry. Lorem Ipsum has been the industry's standard dummy text ever since the 1500s, when an unknown printer took a galley of type and scrambled it to make a type specimen book. It has survived not only five centuries,simply dummy text of the printing and typesetting industry. Lorem Ipsum has been the industry's standard dummy text ever since the 1500s, when an unknown printer took a galley of type and scrambled it to make a type specimen book. It has survived not only five centuries,</p>
    <p>but also the leap into electronic typesetting, remaining essentially unknown &nbsp;printer took a galley of type and scrambled an unknown printer took a galley of type and scrambled unchanged.simply dummy text of the printing and typesetting industry. Lorem Ipsum has been the industry's standard dummy text ever since the 1500s, when an unknown printer took a galley of type and scrambled it to make a type specimen book. It has survived not only five centuries,</p>
    <p class="tight">but also the leap into electronic typesetting, remaining essentially unknown &nbsp;printer took a galley of type and scrambled an unknown printer took a galley of type and scrambled unchanged.</p>
  </div>
  <a class="abs read-more" href="#">read more &gt;&gt;</a>

  <article class="abs card" style="left:86px">
    <span class="card-photo" role="img" aria-label="Two trucks parked side by side" style="background:radial-gradient(circle,#c9ccd1,#3b3f46)"></span>
    <h3 class="card-title">LOREM IPSUM</h3>
    <p class="card-text">Lorem Ipsum is simply dummy text of the pring and typesetting industry. Lorem Ipsum has been the industry's standard.</p>
    <a class="card-btn" href="#">Readmore</a>
  </article>
  <article class="abs card" style="left:242px">
    <span class="card-photo" role="img" aria-label="Truck at a container port" style="background:radial-gradient(circle,#9fb3c8,#59636e)"></span>
    <h3 class="card-title">LOREM IPSUM</h3>
    <p class="card-text">Lorem Ipsum is simply dummy text of the pring and typesetting industry. Lorem Ipsum has been the industry's standard.</p>
    <a class="card-btn" href="#">Readmore</a>
  </article>
  <article class="abs card" style="left:397px">
    <span class="card-photo" role="img" aria-label="Cargo plane in a blue sky" style="background:radial-gradient(circle,#dfe8f5,#3d72b8)"></span>
    <h3 class="card-title">LOREM IPSUM</h3>
    <p class="card-text">Lorem Ipsum is simply dummy text of the pring and typesetting industry. Lorem Ipsum has been the industry's standard.</p>
    <a class="card-btn" href="#">Readmore</a>
  </article>
  <article class="abs card" style="left:552px">
    <span class="card-photo" role="img" aria-label="Warehouse worker with parcels" style="background:radial-gradient(circle,#e0cdb0,#7b6248)"></span>
    <h3 class="card-title">LOREM IPSUM</h3>
    <p class="card-text">Lorem Ipsum is simply dummy text of the pring and typesetting industry. Lorem Ipsum has been the industry's standard.</p>
    <a class="card-btn" href="#">Readmore</a>
  </article>

  <section class="abs partners" aria-label="Partners">
    <svg width="12" height="20" viewBox="0 0 12 20"><path d="M10 2 2 10l8 8" fill="none" stroke="#111" stroke-width="2.4"/></svg>
    <div class="partner-row">
      <span class="partner" style="width:42px"></span>
      <span class="partner" style="width:30px"></span>
      <span class="partner" style="width:30px;height:38px"></span>
      <span class="partner" style="width:60px;height:14px"></span>
      <span class="partner" style="width:42px"></span>
      <span class="partner" style="width:54px"></span>
      <span class="partner" style="width:46px"></span>
      <span class="partner" style="width:22px;border-radius:50%"></span>
    </div>
    <svg width="12" height="20" viewBox="0 0 12 20"><path d="M2 2l8 8-8 8" fill="none" stroke="#111" stroke-width="2.4"/></svg>
  </section>
</main>

<footer>
  <div class="abs footer"></div>
  <div class="abs fcol" style="left:105px">
    <h3>Quick Links</h3>
    <ul><li>Lorem ipsum dolor sit</li><li>Amet consectetuer</li><li>Adipiscing elit</li><li>Praesent vestibulum</li><li>Molestie lacus aenean</li></ul>
  </div>
  <div class="abs fdiv" style="left:229px"></div>
  <div class="abs fcol" style="left:259px;top:1047px">
    <h3>How it Works</h3>
    <ul style="padding-left:2px"><li>Lorem ipsum dolor sit</li><li>Amet consectetuer</li><li>Adipiscing elit</li><li>Praesent vestibulum</li><li>Molestie lacus aenean</li></ul>
  </div>
  <div class="abs fdiv" style="left:385px"></div>
  <div class="abs fcol" style="left:411px;top:1048px">
    <h3>Contact Us</h3>
    <ul style="padding-left:2px"><li>12 Corran Row</li><li>Dunmere, DN4 2QT</li><li>Phone:+44(0)1632 960418</li><li>Email:hello@harlowlogistics.example</li></ul>
  </div>
  <div class="abs flogo"><span class="brand-mark"></span><span class="brand-name">Harlow Logistics</span></div>
  <div class="abs basebar">
    Home <span class="sep">|</span>News <span class="sep">|</span> About Us <span class="sep">|</span> Solutions <span class="sep">|</span> Contact Us
    <span class="copy">© 2014 Logistics</span> &nbsp;FAQ <span class="sep">|</span> Privacy Policy <span class="sep">|</span> Site Map.
  </div>
</footer>

</body>
</html>
```